Torvane Halbridge

Looking for modern business cards.
Clean contemporary design.
Similar to this.
https://www.plumvexa-search.example/imgres?imgurl=https%3A%2F%2Fimg.quorlint-cdn.example%2Fsleek_dark_metal_card_design_540.jpg&imgrefurl=https%3A%2F%2Fwww.quorlint-prints.example%2Fsleek_dark_metal_card_design-918273645501928374&q=modern%20business%20cards

But I'd like the blue to look metallic.

Business

```html
<!DOCTYPE html>
<html lang="en">
<head>
<meta charset="utf-8">
<title>Torvane Halbridge – Business Cards</title>
<link rel="stylesheet" href="https://fonts.googleapis.com/css2?family=Roboto:wght@400;500;700&family=Roboto+Condensed:wght@500&display=swap">
<style>
  :root {
    --navy: #235570;
    --navy-deep: #1c4760;
    --teal: #2a9fc0;
    --teal-band: #269ebb;
    --white: #ffffff;
    --paper: #f4f4f4;
    --backdrop: #e2e2e2;
  }
  * { margin: 0; padding: 0; box-sizing: border-box; }
  html, body { width: 1200px; height: 960px; overflow: hidden; }
  body {
    background: var(--backdrop);
    font-family: "Roboto", Arial, sans-serif;
    position: relative;
  }
  .card {
    position: absolute;
    width: 601px;
    height: 343px;
    overflow: hidden;
  }
  .card-front {
    left: 314px; top: 113px;
    background: linear-gradient(135deg, var(--navy) 0%, #2a6685 45%, var(--navy-deep) 100%);
  }
  .card-back {
    left: 311px; top: 472px;
    background: var(--paper);
  }
  .front-arc { position: absolute; left: 0; top: 0; }
  .front-brand {
    position: absolute;
    left: 33px; top: 254px;
    color: var(--navy);
    font-size: 26px;
    font-weight: 400;
    letter-spacing: -0.3px;
    white-space: nowrap;
  }
  .tagline {
    position: absolute;
    color: var(--teal);
    font-size: 7px;
    font-weight: 700;
    font-style: italic;
    letter-spacing: 0.8px;
    white-space: nowrap;
  }
  .front-tagline { left: 98px; top: 294px; }
  .contact {
    position: absolute;
    right: 26px; top: 48px;
    text-align: right;
    color: var(--white);
  }
  .contact-name {
    font-family: "Roboto Condensed", "Arial Narrow", sans-serif;
    font-weight: 500;
    font-size: 26px;
    line-height: 30px;
    color: var(--teal);
  }
  .contact-role {
    font-weight: 500;
    font-size: 15px;
    line-height: 20px;
    letter-spacing: 0.3px;
  }
  .contact-address, .contact-lines {
    font-size: 15px;
    line-height: 19px;
  }
  .contact-address { margin-top: 62px; }
  .contact-lines { margin-top: 12px; }
  .contact-label { color: var(--teal); font-weight: 700; }
  .back-brand {
    position: absolute;
    left: 0; right: 0; top: 134px;
    text-align: center;
    color: var(--navy);
    font-size: 36px;
    font-weight: 400;
    letter-spacing: -0.4px;
  }
  .back-tagline {
    left: 0; right: 0; top: 184px;
    text-align: center;
  }
  .web-band {
    position: absolute;
    left: 0; top: 285px;
    width: 100%; height: 32px;
    background: linear-gradient(180deg, #36b2cf 0%, var(--teal-band) 50%, #1f8aa6 100%);
    color: var(--white);
    font-size: 15px;
    letter-spacing: 3.2px;
    line-height: 32px;
    text-align: center;
  }
</style>
</head>
<body>
  <section class="card card-front">
    <svg class="front-arc" width="601" height="343" viewBox="0 0 601 343" aria-hidden="true">
      <circle cx="175" cy="320" r="185" fill="#ffffff"/>
    </svg>
    <div class="front-brand">Torvane Halbridge</div>
    <div class="tagline front-tagline">"Steady guidance for companies on the rise"</div>
    <div class="contact">
      <div class="contact-name">MARLOW FENWICK</div>
      <div class="contact-role">CEO/FOUNDER</div>
      <div class="contact-address">4120 Quillmere Lane<br>Dunmore Bay, Alaska 34572</div>
      <div class="contact-lines">
        <div><span class="contact-label">P:</span> 555 214 7730</div>
        <div><span class="contact-label">M:</span> 555 382 6105</div>
        <div><span class="contact-label">F:</span> 555 907 4418</div>
        <div>hello@torvane.example</div>
        <div>www.torvane.example</div>
      </div>
    </div>
  </section>

  <section class="card card-back">
    <div class="back-brand">Torvane Halbridge</div>
    <div class="tagline back-tagline">"Steady guidance for companies on the rise"</div>
    <div class="web-band">www.torvanehalbridge.example</div>
  </section>
</body>
</html>
```